Kickbut Home Page Design built to Sell

We need a new home page layout. The website is working now but we need a refresh. Our business has slowed down since a few years ago. We need to show we build ecommerce and membership websites. Here is the page now: https://www.brelvoxstudio.graphics/new-home/

Target Market(s)

Women, solopreneurs, artists, politicians

Industry/Entity Type

Design Agency

Number of Pages Required

1 page

Font styles to use
Sans Serif

Colors
b8a6cd
fabb94
acd136
00a990

Requirements
Must have
• Video header
Section for text and Step process similar to this website: https://quintarelweb.com/ [This is out sister company]
Places for images.
Call to action lead gen form and Get a quote.
The menu should show WEB, PRINT, VIDEO
Nice to have
• I LOVE this company: https://tarnwickly.com/guide/
Area for testimonials
Should not have
• We don't want a duplicate of https://quintarelweb.com/

```html
<!DOCTYPE html>
<html lang="en">
<head>
<meta charset="utf-8">
<title>Brelvox Studio — Web Design Agency</title>
<link rel="stylesheet" href="https://fonts.googleapis.com/css2?family=Poppins:wght@500;600;700&family=Sarabun:wght@400;500;600&display=swap">
<style>
:root{
  --green:#8cc63f;
  --teal:#139e7f;
  --ink:#1c1c1c;
  --body:#3a3a3a;
  --muted:#666;
  --blush:#f4f0f0;
  --line:#d9d9d9;
  --footer:#232323;
  --white:#fff;
}
*{margin:0;padding:0;box-sizing:border-box}
html,body{width:1200px;height:4237px;overflow:hidden;background:var(--white)}
body{position:relative;font-family:"Sarabun",sans-serif;color:var(--body)}
.abs{position:absolute}
.head{font-family:"Poppins",sans-serif;font-weight:600;color:var(--ink);letter-spacing:.3px}
.btn{position:absolute;background:var(--green);color:var(--white);font-family:"Poppins",sans-serif;font-weight:600;display:flex;align-items:center;justify-content:center;letter-spacing:.4px}
.photo{position:absolute}

/* hero */
.hero{position:absolute;left:0;top:0;width:1200px;height:676px;background:linear-gradient(100deg,#6d6a66 0%,#9b958d 35%,#cfc8bd 60%,#e4ded5 100%)}
.hero-shade{position:absolute;inset:0;background:linear-gradient(90deg,rgba(30,30,30,.55) 0%,rgba(30,30,30,.25) 45%,rgba(0,0,0,0) 70%)}
.brand{position:absolute;left:39px;top:34px;color:var(--white)}
.brand-name{font-family:"Poppins",sans-serif;font-weight:600;font-size:34px;letter-spacing:1px;line-height:1}
.brand-tag{font-family:"Sarabun",sans-serif;font-size:9.5px;letter-spacing:2.4px;margin-top:6px}
.nav a{position:absolute;top:30px;color:var(--white);font-family:"Poppins",sans-serif;font-weight:600;font-size:18px;text-decoration:none}
.hero-title{position:absolute;left:77px;top:246px;font-family:"Poppins",sans-serif;font-weight:700;font-size:30px;line-height:44.5px;color:var(--white);text-transform:uppercase}
.play{position:absolute;left:602px;top:283px}

/* agency */
.agency-text{position:absolute;left:625px;top:762px;width:450px}
.agency-text h2{font-size:21px}
.lead{font-size:15px;line-height:21px;color:var(--ink);margin-top:16px}
.small{font-size:13px;line-height:20.6px;color:var(--body);margin-top:17px}

/* steps */
.steps-band{position:absolute;left:0;top:1185px;width:584px;height:526px;background:var(--blush)}
.step-icon{position:absolute;left:130px;width:78px;height:78px;border-radius:50%;background:var(--teal)}
.step{position:absolute;left:230px;width:240px}
.step .num{font-size:12px;color:var(--ink)}
.step h3{font-family:"Poppins",sans-serif;font-weight:500;font-size:17px;color:var(--ink);margin-top:2px}
.step p{font-size:12.5px;line-height:18px;color:var(--body);margin-top:4px}

/* headings centered */
.center-head{position:absolute;left:0;width:1200px;text-align:center;font-size:21px}
.rule{position:absolute;left:570px;width:60px;height:2px;background:#bbb}

/* testimonials */
.card{position:absolute;top:1861px;width:298px;height:365px;border:1px solid var(--line);background:var(--white)}
.card .q{position:absolute;left:24px;top:14px;color:var(--teal);font-family:Georgia,serif;font-size:32px;font-weight:700}
.card p{position:absolute;left:41px;top:54px;width:232px;font-size:13px;line-height:20px;color:var(--body)}
.person{position:absolute;top:2206px}
.avatar{position:absolute;width:40px;height:40px;border-radius:50%;background:linear-gradient(#c9c3bc,#7a746e)}
.who{position:absolute;font-size:12px;line-height:13px;color:var(--ink);white-space:nowrap}
.who b{font-weight:500;display:block}
.arrow{position:absolute;top:2035px;width:41px;height:27px;background:var(--teal);display:flex;align-items:center;justify-content:center}

/* work */
.work-band{position:absolute;left:0;top:2331px;width:1200px;height:875px;background:var(--blush)}
.label{position:absolute;width:300px;text-align:center;font-family:"Poppins",sans-serif;font-weight:500;font-size:15px;color:var(--ink)}

/* quote */
.footer-band{position:absolute;left:0;top:3789px;width:1200px;height:448px;background:var(--footer)}
.form-card{position:absolute;left:225px;top:3362px;width:750px;height:534px;background:var(--white);box-shadow:0 2px 18px rgba(0,0,0,.08)}
.field{position:absolute;border:1px solid #9c9c9c;height:42px;font-size:12px;color:var(--body);padding:13px 14px}
.field.msg{height:115px}
.chev{position:absolute;right:14px;top:15px}

/* footer */
.foot-h{position:absolute;font-family:"Poppins",sans-serif;font-weight:600;font-size:12px;color:var(--white);letter-spacing:.5px}
.foot-t{position:absolute;font-size:11.5px;line-height:16px;color:#d6d6d6}
.foot-ico{position:absolute;width:22px;height:22px;border-radius:50%;background:var(--white)}
.foot-rule{position:absolute;left:148px;top:4159px;width:912px;height:1px;background:#444}
.copy{position:absolute;left:0;top:4190px;width:1200px;text-align:center;font-size:10.5px;color:#bbb}
</style>
</head>
<body>

<!-- Hero -->
<section class="hero" role="img" aria-label="Looping header video: smiling man in glasses working on a laptop in a bright office">
  <div class="hero-shade"></div>
</section>
<div class="brand">
  <div class="brand-name">BRELVOX STUDIO</div>
  <div class="brand-tag">GRAPHICS WEB VIDEO CONSULTANTS</div>
</div>
<nav class="nav">
  <a style="left:887px">WEB</a>
  <a style="left:977px">PRINT</a>
  <a style="left:1081px">VIDEO</a>
</nav>
<h1 class="hero-title">Lead generating<br>websites that move<br>your business forward</h1>
<div class="btn" style="left:82px;top:401px;width:222px;height:53px;font-size:17px">GET A FREE QUOTE</div>
<svg class="play" width="56" height="56" viewBox="0 0 56 56" aria-label="Play video">
  <circle cx="28" cy="28" r="28" fill="#fff"/>
  <path d="M22 16 L39 28 L22 40 Z" fill="#333"/>
</svg>

<!-- Agency intro -->
<div class="photo" style="left:0;top:732px;width:580px;height:394px;background:linear-gradient(135deg,#6f5f55 0%,#9a8f86 45%,#d6d2cc 60%,#5c5b64 100%)" role="img" aria-label="Hands typing on a laptop showing the studio name, beside a notebook and pens on a wooden desk"></div>
<div class="agency-text">
  <h2 class="head">WE ARE A WEB DESIGN AGENCY</h2>
  <p class="lead">We help brands sell online with beautifully designed websites and effective digital marketing strategies that deliver results &amp; help your business grow.</p>
  <p class="small">Quintarel Designs is a New England web design agency providing high quality, professional and reliable website - webpage design and graphic design services to individuals, nonprofits, small - medium sized businesses, and political campaigns. We are a small team of highly professional web consultants with over 20 years of knowledge and experience and we'd love to help you too!</p>
</div>
<div class="btn" style="left:628px;top:1046px;width:128px;height:41px;font-size:14px">CONTACT US</div>

<!-- How it works -->
<div class="steps-band"></div>
<div class="photo" style="left:584px;top:1185px;width:616px;height:526px;background:linear-gradient(120deg,#3a3835 0%,#5d5a55 40%,#b8b6b2 75%,#8a8986 100%)" role="img" aria-label="Woman smiling while working at a desktop computer in a modern office"></div>
<h2 class="head abs" style="left:128px;top:1230px;font-size:20px">HOW IT WORKS</h2>

<svg class="step-icon" style="top:1301px" viewBox="0 0 78 78" aria-hidden="true">
  <circle cx="39" cy="39" r="39" fill="#139e7f"/>
  <rect x="27" y="23" width="24" height="31" rx="3" fill="none" stroke="#fff" stroke-width="2.6"/>
  <path d="M32 32h14M32 38h14M32 44h10" stroke="#fff" stroke-width="2.4"/>
</svg>
<div class="step" style="top:1301px"><div class="num">STEP 1</div><h3>TELL US YOUR NEEDS</h3><p>Lorem Ipsum is simply dummy text of the printing</p></div>

<svg class="step-icon" style="top:1436px" viewBox="0 0 78 78" aria-hidden="true">
  <circle cx="39" cy="39" r="39" fill="#139e7f"/>
  <path d="M28 24c-3 2-4 5-3 9 2 8 9 16 17 19 4 1 7 0 9-3l-5-5-4 2c-4-2-7-5-9-9l2-4z" fill="none" stroke="#fff" stroke-width="2.6" stroke-linejoin="round"/>
  <path d="M42 26a10 10 0 0 1 9 9M42 20a16 16 0 0 1 15 15" fill="none" stroke="#fff" stroke-width="2.4"/>
</svg>
<div class="step" style="top:1436px"><div class="num">STEP 2</div><h3>PHONE CALL</h3><p>Lorem Ipsum is simply dummy text of the printing</p></div>

<svg class="step-icon" style="top:1572px" viewBox="0 0 78 78" aria-hidden="true">
  <circle cx="39" cy="39" r="39" fill="#139e7f"/>
  <path d="M44 26H28a3 3 0 0 0-3 3v21a3 3 0 0 0 3 3h21a3 3 0 0 0 3-3V35" fill="none" stroke="#fff" stroke-width="2.6"/>
  <path d="M50 22l6 6-15 15-8 2 2-8z" fill="none" stroke="#fff" stroke-width="2.6" stroke-linejoin="round"/>
</svg>
<div class="step" style="top:1572px"><div class="num">STEP 3</div><h3>CUSTOM QUOTE ARRIVES</h3><p>Lorem Ipsum is simply dummy text of the printing</p></div>

<!-- Testimonials -->
<h2 class="head center-head" style="top:1770px">TESTIMONIALS</h2>
<div class="rule" style="top:1813px"></div>

<div class="arrow" style="left:61px"><svg width="12" height="14" viewBox="0 0 12 14"><path d="M8 2 3 7l5 5" fill="none" stroke="#fff" stroke-width="2"/></svg></div>
<div class="arrow" style="left:1095px"><svg width="12" height="14" viewBox="0 0 12 14"><path d="M4 2l5 5-5 5" fill="none" stroke="#fff" stroke-width="2"/></svg></div>

<div class="card" style="left:132px"><span class="q">“</span><p>Dana Whitlow was great to work with and extremely knowledgeable and accessible. I especially appreciated his well thought out design process and the client videos he created to walk me through various stages of it. I received lots of great feedback on the visual look, user-friendliness, and rich content of my website throughout the campaign and was re-elected overwhelmingly. I highly recommend Dana and Quintarel Designs for your next project!</p></div>
<div class="card" style="left:450px"><span class="q">“</span><p>There are many variations of passages of Lorem Ipsum available, but the majority have suffered alteration in some form, by injected humour, or randomised words which don't look even slightly believable. If you are going to use a passage of Lorem Ipsum, you need to be sure there isn't anything embarrassing hidden in the middle of text. All the Lorem Ipsum generators on the Internet tend to repeat predefined chunks as necessary.</p></div>
<div class="card" style="left:769px"><span class="q">“</span><p>There are many variations of passages of Lorem Ipsum available, but the majority have suffered alteration in some form, by injected humour, or randomised words which don't look even slightly believable. If you are going to use a passage of Lorem Ipsum, you need to be sure there isn't anything embarrassing hidden in the middle of text. All the Lorem Ipsum generators on the Internet tend to repeat predefined chunks as necessary.</p></div>

<div class="avatar" style="left:174px;top:2206px" role="img" aria-label="Client portrait"></div>
<div class="who" style="left:229px;top:2214px"><b>MARTIN HALVORSEN</b>MAYOR, EASTBROOK, MA</div>
<div class="avatar" style="left:493px;top:2206px" role="img" aria-label="Client portrait"></div>
<div class="who" style="left:548px;top:2214px"><b>MARTIN HALVORSEN</b>MAYOR, EASTBROOK, MA</div>
<div class="avatar" style="left:812px;top:2206px" role="img" aria-label="Client portrait"></div>
<div class="who" style="left:866px;top:2214px"><b>MARTIN HALVORSEN</b>MAYOR, EASTBROOK, MA</div>

<!-- Work -->
<div class="work-band"></div>
<h2 class="head center-head" style="top:2373px">EXAMPLES OF OUR WORK</h2>
<div class="rule" style="top:2417px"></div>

<div class="photo" style="left:132px;top:2454px;width:297px;height:252px;background:linear-gradient(160deg,#e8e6e3,#b9b5b0)" role="img" aria-label="Responsive website shown on laptop, tablet and phone"></div>
<div class="photo" style="left:449px;top:2454px;width:297px;height:252px;background:linear-gradient(160deg,#e3ddd6,#c7c2bc)" role="img" aria-label="Web design mockup on desktop, laptop, tablet and phone"></div>
<div class="photo" style="left:769px;top:2454px;width:298px;height:252px;background:linear-gradient(160deg,#6e7f95,#c9c2b8 60%,#3f4c5c)" role="img" aria-label="Printed magazine pages fanned open"></div>
<div class="label" style="left:130px;top:2731px">LOREM IPSUM</div>
<div class="label" style="left:447px;top:2731px">LOREM IPSUM</div>
<div class="label" style="left:768px;top:2731px">LOREM IPSUM</div>

<div class="photo" style="left:132px;top:2778px;width:297px;height:252px;background:linear-gradient(160deg,#3c4a2e,#2a2a2a 60%,#6a7a50)" role="img" aria-label="Website mockup on a tablet and phone with a plant"></div>
<div class="photo" style="left:449px;top:2778px;width:297px;height:252px;background:linear-gradient(160deg,#f2b733,#2d8ccf 50%,#e8e4de)" role="img" aria-label="Colourful web design shown on a desktop monitor with paint splashes"></div>
<div class="photo" style="left:769px;top:2778px;width:298px;height:252px;background:linear-gradient(160deg,#d9d5cf,#b38a5e 75%,#e6e2dc)" role="img" aria-label="Website on desktop, laptop and tablet on a wooden desk"></div>
<div class="label" style="left:130px;top:3055px">LOREM IPSUM</div>
<div class="label" style="left:447px;top:3055px">LOREM IPSUM</div>
<div class="label" style="left:768px;top:3055px">LOREM IPSUM</div>

<div class="btn" style="left:513px;top:3122px;width:159px;height:43px;font-size:14px">VIEW ALL WORKS</div>

<!-- Quote form -->
<h2 class="head center-head" style="top:3269px">GET A QUOTE</h2>
<div class="rule" style="top:3313px"></div>
<div class="footer-band"></div>
<form class="form-card" aria-label="Quote request form"></form>
<div class="field" style="left:276px;top:3410px;width:314px">First Name</div>
<div class="field" style="left:610px;top:3410px;width:316px">Last Name</div>
<div class="field" style="left:276px;top:3471px;width:314px">Email</div>
<div class="field" style="left:610px;top:3471px;width:316px">Phone</div>
<div class="field" style="left:276px;top:3533px;width:314px">Company Name</div>
<div class="field" style="left:610px;top:3533px;width:316px">Job Title</div>
<div class="field" style="left:276px;top:3594px;width:314px">State / Province</div>
<div class="field" style="left:610px;top:3594px;width:316px">Country<svg class="chev" width="12" height="8" viewBox="0 0 12 8"><path d="M1 1l5 5 5-5" fill="none" stroke="#333" stroke-width="1.6"/></svg></div>
<div class="field msg" style="left:276px;top:3658px;width:650px">Write Message</div>
<div class="btn" style="left:549px;top:3811px;width:100px;height:41px;font-size:14px">SUBMIT</div>

<!-- Footer -->
<div class="brand" style="left:148px;top:3993px">
  <div class="brand-name" style="font-size:32px">BRELVOX STUDIO</div>
  <div class="brand-tag" style="font-size:9px">GRAPHICS WEB VIDEO CONSULTANTS</div>
</div>

<div class="foot-h" style="left:477px;top:3941px">MENU</div>
<div class="foot-t" style="left:477px;top:3979px;line-height:19.6px">WEB<br>PRINT<br>VIDEO</div>

<div class="foot-h" style="left:667px;top:3941px">CONTACT US</div>
<svg class="foot-ico" style="left:666px;top:3984px" viewBox="0 0 22 22"><circle cx="11" cy="11" r="11" fill="#fff"/><path d="M11 5a4 4 0 0 0-4 4c0 3 4 8 4 8s4-5 4-8a4 4 0 0 0-4-4z" fill="#232323"/><circle cx="11" cy="9" r="1.4" fill="#fff"/></svg>
<div class="foot-t" style="left:699px;top:3982px">18 Linden Row,<br>Marlow MA 01090</div>
<svg class="foot-ico" style="left:666px;top:4035px" viewBox="0 0 22 22"><circle cx="11" cy="11" r="11" fill="#fff"/><path d="M8 6c-2 1-2 3-1 5 1 2 3 4 5 5 2 1 4 1 5-1l-2-2-2 1c-1-1-2-2-3-3l1-2z" fill="#232323"/></svg>
<div class="foot-t" style="left:699px;top:4033px">Call Us<br>1-555-014-2290</div>
<svg class="foot-ico" style="left:666px;top:4086px" viewBox="0 0 22 22"><circle cx="11" cy="11" r="11" fill="#fff"/><rect x="6" y="7.5" width="10" height="7" fill="#232323"/><path d="M6 7.5l5 4 5-4" fill="none" stroke="#fff" stroke-width="1"/></svg>
<div class="foot-t" style="left:699px;top:4084px">E mail Us<br>dana@quintareldesign.com</div>

<div class="foot-h" style="left:960px;top:3941px">FOLLOW US</div>
<div class="foot-ico" style="left:959px;top:3984px"></div>
<div class="foot-t" style="left:993px;top:3982px">Like us on<br>FRIENDLINE</div>
<div class="foot-ico" style="left:959px;top:4035px"></div>
<div class="foot-t" style="left:993px;top:4033px">Follow us on<br>CHIRPNET</div>
<div class="foot-ico" style="left:959px;top:4086px"></div>
<div class="foot-t" style="left:993px;top:4084px">Follow us on<br>WORKLINK</div>

<div class="foot-rule"></div>
<div class="copy">Copyright © 2021 All Rights Reserved</div>

</body>
</html>
```